Trade show flier

Need a two sided flier for a trade show that will go with the trade show banner you are designing for us. We have included some information we would like to see o the flier. We do need to work on the content. If you can start a design, we can work on the content. This must be done by 3/12/2018

Target Market(s)

Manufacturing companies

Industry/Entity Type

Trade

```html
<!DOCTYPE html>
<html lang="en">
<head>
<meta charset="utf-8">
<title>Linkwright Systems – Trade Show Flier</title>
<link rel="stylesheet" href="https://fonts.googleapis.com/css2?family=Oswald:wght@400;500;600&family=PT+Sans:wght@400;700&display=swap">
<style>
:root{
  --blue:#1b6fbf;
  --blue-dark:#14549a;
  --blue-light:#b9d4ee;
  --orange:#f37f22;
  --orange-soft:#f79a4a;
  --ink:#2b2b2b;
  --grey:#555b63;
  --footer:#2a2c30;
  --page:#ebe8e3;
  --white:#ffffff;
}
*{box-sizing:border-box;margin:0;padding:0}
html,body{width:1200px;height:774px;overflow:hidden}
body{background:var(--page);font-family:"PT Sans",Arial,sans-serif;color:var(--ink);position:relative}
h1,h2,p,ul{margin:0;font-weight:inherit}
.flier{position:absolute;top:77px;width:490px;height:634px;background:var(--white);overflow:hidden;box-shadow:0 4px 14px rgba(0,0,0,.25)}
.flier--front{left:86px}
.flier--back{left:627px}
.abs{position:absolute}
.shapes{position:absolute;left:0;top:0}

/* photo areas */
.photo{position:absolute;left:0;top:0;width:490px}
.photo--front{height:300px;background:linear-gradient(100deg,#1c2230 0%,#3a3a32 45%,#8a7a3a 62%,#c7b25a 75%,#3d3a30 100%)}
.photo--back{height:270px;background:linear-gradient(100deg,#2b4f86 0%,#3b6fb5 35%,#8fb6d8 60%,#4f86c0 80%,#1f3f70 100%)}

/* headline */
.headline{left:20px;top:45px;font-family:"Oswald",sans-serif;font-weight:500;font-size:26px;line-height:40px;color:var(--white);letter-spacing:-.5px;text-transform:uppercase;white-space:nowrap}
.headline .hl{color:var(--orange)}

/* tabs */
.tab{left:6px;width:156px;height:22px;background:var(--orange);color:var(--white);font-size:10.5px;line-height:22px;padding-left:8px;border-radius:0 11px 11px 0;text-transform:uppercase;white-space:nowrap;box-shadow:0 2px 3px rgba(0,0,0,.25)}
.about-text,.diff-text{left:19px;width:177px;font-size:7.6px;line-height:10.45px;color:var(--white);text-align:justify}
.diff-sub{left:19px;font-size:7.6px;color:var(--orange-soft);text-transform:uppercase}

/* brand */
.brand{display:flex;align-items:center;gap:9px}
.brand__mark{width:48px;height:48px;border-radius:50%;background:var(--blue);flex:none}
.brand__name{font-family:"PT Sans",sans-serif;font-weight:700;color:var(--blue);font-size:30px;line-height:30px;letter-spacing:.5px;text-transform:lowercase}
.brand__name small{display:block;font-size:15px;line-height:18px;letter-spacing:6px}

/* services */
.services-title{left:230px;top:338px;font-family:"Oswald",sans-serif;font-weight:500;font-size:19px;line-height:22px;color:var(--blue);border-bottom:1.5px solid var(--blue);padding-bottom:3px;white-space:nowrap}
.services{left:231px;top:378px;width:250px;list-style:none}
.services li{position:relative;padding-left:17px;font-size:6.6px;line-height:8px;color:var(--grey);margin-bottom:5.2px}
.services li::before{content:"";position:absolute;left:2px;top:1px;width:8px;height:8px;border-radius:50%;background:var(--orange)}
.services b{font-family:"Oswald",sans-serif;font-weight:500;font-size:8px;color:var(--blue);text-transform:uppercase}

/* footer */
.footer{left:0;top:593px;width:490px;height:41px;background:linear-gradient(90deg,#3a3c40,var(--footer));display:flex;align-items:center;padding-left:19px;font-size:9.6px;color:var(--white);white-space:nowrap}
.footer .dot{width:9px;height:9px;border-radius:50%;background:var(--orange);display:inline-block;margin:0 5px 0 8px}
.phone{left:339px;top:589px;width:151px;height:45px;background:var(--orange);color:var(--white);font-size:17px;display:flex;align-items:center;justify-content:center;gap:6px;white-space:nowrap}

/* back side */
.support{left:356px;top:204px;width:140px;font-family:"Oswald",sans-serif;font-weight:500;color:var(--white);text-align:center;font-size:27px;line-height:33px;letter-spacing:.5px}
.box{left:15px;top:341px;width:459px;height:179px;border:1.3px solid #6d8fb8;border-radius:8px}
.box-title{left:95px;top:329px;width:300px;height:26px;background:var(--orange);color:var(--white);border-radius:13px;font-size:11.5px;line-height:26px;font-weight:400;text-align:center;text-transform:uppercase;white-space:nowrap;box-shadow:0 2px 3px rgba(0,0,0,.25)}
.bullets{list-style:none;font-size:9.2px;letter-spacing:-.1px;line-height:18.4px;color:var(--ink);white-space:nowrap}
.bullets li::before{content:"•";color:var(--orange);margin-right:3px}
.bullets--a{left:25px;top:364px}
.bullets--b{left:244px;top:364px}
.partners-title{left:0;top:532px;width:490px;text-align:center;font-size:8.3px;color:var(--grey);text-transform:uppercase;letter-spacing:.3px}
.partners{left:14px;top:558px;width:462px;display:flex;justify-content:space-between;align-items:center}
.partner{height:18px;background:#c9ccd1;border-radius:3px}
</style>
</head>
<body>

<!-- FRONT -->
<section class="flier flier--front">
  <div class="photo photo--front" role="img" aria-label="Engineer in hard hat and safety vest reviewing a tablet on a factory floor"></div>
  <svg class="shapes" width="490" height="634" viewBox="0 0 490 634" aria-hidden="true">
    <path d="M206 236 Q330 220 490 252 L490 262 Q330 230 206 246 Z" fill="var(--blue-light)"/>
    <path d="M206 246 Q330 230 490 262 L490 634 L206 634 Z" fill="var(--white)"/>
    <path d="M0 262 Q5 259 10 257 L10 634 L0 634 Z" fill="var(--white)"/>
    <path d="M10 257 Q110 232 206 224 L206 634 L10 634 Z" fill="var(--blue)"/>
    <path d="M206 224 L206 300 Q205 242 196 225 Z" fill="var(--blue-dark)"/>
  </svg>

  <h1 class="abs headline">We maximize <span class="hl">production</span><br><span class="hl">up time</span> by reducing<br>network downtime</h1>

  <div class="abs tab" style="top:285px">About us</div>
  <p class="abs about-text" style="top:317px">Linkwright IT was founded in 2006 with the fundamental belief that our company is first in the business of providing great customer service, and second, as a first-class IT service provider. When partnering with us, you are not just hiring an IT support company - you're choosing an IT partner to help navigate your company through business technology decisions. We know as you grow, our business will grow as well, therefore, we will always provide you with a competitive advantage.</p>

  <div class="abs tab" style="top:445px">What makes us different</div>
  <p class="abs diff-sub" style="top:472px">Why we are different</p>
  <p class="abs diff-text" style="top:488px">What differentiates Linkwright IT from the competition is our core values and belief in PEOPLE, PASSION, and PRIDE. These core values ensure our customer gets the very best technical results from our team of experts along with an entire team that they can feel comfortable communicating with. We have a passion for technology and take great pride in everything we do.</p>

  <div class="abs brand" style="left:228px;top:271px">
    <span class="brand__mark"></span>
    <span class="brand__name">linkwright<small>systems</small></span>
  </div>

  <h2 class="abs services-title">OUR SERVICES</h2>
  <ul class="abs services">
    <li><b>Managed services -</b> 24x7 Proactive support, remediation and maintenance of your technology infrastructure</li>
    <li><b>Backup &amp; business continuity -</b> Reliable Data Protection &amp; Disaster Recovery Services</li>
    <li><b>Virtualization -</b> Increase IT flexibility and scalability while minimizing hardware resources.</li>
    <li><b>Telecom -</b> Voice-over-IP (VOIP) Design and Deployment.</li>
    <li><b>Cloud services -</b> Use the power of the cloud to accelerate your business</li>
    <li><b>Network security -</b> Multi-layered approach to addressing your network security.</li>
    <li><b>Wireless services -</b> Secure connectivity and centralized management for wireless endpoint devices.</li>
    <li><b>Procurement services -</b> Procurement of industry standard business class products and software</li>
    <li><b>Project management -</b> Design and Management of Business Critical Projects.</li>
    <li><b>Video surveillance -</b> Security Video Surveillance</li>
  </ul>

  <div class="abs footer">For more information:<span class="dot"></span>sales@lwsys.com<span class="dot"></span>www.lwsys.com</div>
  <div class="abs phone">
    <svg width="14" height="14" viewBox="0 0 24 24" aria-hidden="true"><path fill="none" stroke="#fff" stroke-width="2" d="M6.6 3h3l1.5 4.5-2 1.5a11 11 0 0 0 5.9 5.9l1.5-2 4.5 1.5v3a2 2 0 0 1-2 2A17 17 0 0 1 4.6 5a2 2 0 0 1 2-2z"/></svg>
    209-555-0172
  </div>
</section>

<!-- BACK -->
<section class="flier flier--back">
  <div class="photo photo--back" role="img" aria-label="Technician in blue coveralls working on a laptop beside an industrial control cabinet"></div>
  <svg class="shapes" width="490" height="634" viewBox="0 0 490 634" aria-hidden="true">
    <path d="M0 232 Q200 250 490 235 L490 250 Q200 268 0 244 Z" fill="var(--blue-light)"/>
    <path d="M0 244 Q200 268 490 250 L490 634 L0 634 Z" fill="var(--white)"/>
    <circle cx="437" cy="236" r="78" fill="var(--orange)" opacity=".92"/>
    <circle cx="353" cy="275" r="22" fill="var(--orange)"/>
  </svg>
  <p class="abs support">24x7<br>SUPPORT</p>

  <div class="abs brand" style="left:20px;top:265px">
    <span class="brand__mark"></span>
    <span class="brand__name">linkwright<small>systems</small></span>
  </div>

  <div class="abs box"></div>
  <h2 class="abs box-title">Managed services support include</h2>
  <ul class="abs bullets bullets--a">
    <li>Team of industry certified Network Engineers</li>
    <li>Unlimited Remote Support (Weekdays 7am – 6pm)</li>
    <li>Unlimited Onsite Support (Weekdays 7am – 6pm)</li>
    <li>24x7 network monitoring and remediation.</li>
    <li>Daily proactive maintenance</li>
    <li>Managed antivirus software</li>
    <li>Managed ransomware protection</li>
    <li>Ticketing portal to track open tickets and resolutions</li>
  </ul>
  <ul class="abs bullets bullets--b">
    <li>Vendor management</li>
    <li>Network Documentation Management</li>
    <li>Software License Management</li>
    <li>Technology procurement</li>
    <li>Monitoring of existing backup systems and data recovery</li>
    <li>Business continuity planning</li>
    <li>Network and data security planning and testing</li>
    <li>Quarterly IT meetings</li>
  </ul>

  <p class="abs partners-title">Our technology partners</p>
  <div class="abs partners" role="list" aria-label="Technology partner badges">
    <span class="partner" role="listitem" style="width:54px"></span>
    <span class="partner" role="listitem" style="width:36px"></span>
    <span class="partner" role="listitem" style="width:70px"></span>
    <span class="partner" role="listitem" style="width:30px"></span>
    <span class="partner" role="listitem" style="width:28px"></span>
    <span class="partner" role="listitem" style="width:56px"></span>
    <span class="partner" role="listitem" style="width:70px"></span>
    <span class="partner" role="listitem" style="width:56px"></span>
  </div>

  <div class="abs footer">For more information:<span class="dot"></span>sales@lwsys.com<span class="dot"></span>www.lwsys.com</div>
  <div class="abs phone">
    <svg width="14" height="14" viewBox="0 0 24 24" aria-hidden="true"><path fill="none" stroke="#fff" stroke-width="2" d="M6.6 3h3l1.5 4.5-2 1.5a11 11 0 0 0 5.9 5.9l1.5-2 4.5 1.5v3a2 2 0 0 1-2 2A17 17 0 0 1 4.6 5a2 2 0 0 1 2-2z"/></svg>
    209-555-0172
  </div>
</section>

</body>
</html>
```